BrivoTerna. Lantern of the Steady Harvest. Business card

Professional business card for BrivoTerna (Lantern of the Steady Harvest)
My rationale: Strategy-> Execution-> Results-> Value that lead to the BrivoTerna name: We put the Lantern of the Steady Harvest.
We deliver value to our customers helping them at defining a good strategy (cyan arrow). 90% of well formulated strategies fail due to poor execution so we also consider strategical execution very important (green arrow). Due to the execution we obtain the results (blue arrow). Finally, the results provide feedback to redefine strategy, and the new strategy has to be executed and new results obtained providing new feedback and on and on. It's like a wheel that finally, must create corporate value: value for shareholders, staholders, employees, providers...-

Target Market(s)

CEOs and steering comitees , invewrnent funds

Industry/Entity Type

Business Consultant

Contact Information for Business Card

Teodoro Vinsquel
CEO & Founder
teodoro.vinsquel@brivoterna-example.com
Mobile: +34 655.803.912
www.brivoterna-example.com

Colors

Designer to choose colors to be used in the design.

Requirements
Nice to have
• Nice to hace the words: Strategy, execution, results
• Nice to vave the claim: Lantern of the Steady Harvest
• The three colors should be shown:
• cyan for STRATEGY
• green for EXECUTION
• blue for RESULTS
Should not have
• Complete black background

```html
<!DOCTYPE html>
<html lang="en">
<head>
<meta charset="utf-8">
<title>BrivoTerna – Business Card</title>
<link rel="stylesheet" href="https://fonts.googleapis.com/css2?family=Open+Sans:wght@400;700&display=swap">
<style>
  :root {
    --bg: #e6e3e0;
    --card: #ffffff;
    --navy: #1b3a96;
    --band: #0f3399;
    --band-dark: #0a2a80;
    --cyan: #1fa8e6;
    --faint: #e8eef8;
    --white: #ffffff;
  }
  * { margin: 0; padding: 0; box-sizing: border-box; }
  html, body {
    width: 1200px; height: 997px; overflow: hidden;
    background: var(--bg);
    font-family: "Open Sans", Arial, sans-serif;
  }
  .stage { position: relative; width: 1200px; height: 997px; }
  .card {
    position: absolute; width: 560px; height: 320px;
    background: var(--card);
    box-shadow: 0 6px 18px rgba(0,0,0,0.12);
    overflow: hidden;
  }
  .card--front { left: 70px; top: 110px; }
  .card--back { left: 570px; top: 560px; }

  .wordmark {
    position: absolute; left: 0; right: 0;
    text-align: center; font-weight: 700;
    color: var(--navy); letter-spacing: -0.5px;
  }
  .card--front .wordmark { top: 70px; font-size: 40px; }

  .contact-band {
    position: absolute; left: 215px; right: 0; top: 160px; height: 78px;
    background: var(--band);
  }
  .icon-strip {
    position: absolute; left: 215px; top: 160px; width: 26px; height: 78px;
    background: var(--band-dark);
    display: flex; flex-direction: column; justify-content: space-evenly; align-items: center;
  }
  .icon-strip svg { width: 11px; height: 11px; }
  .contact-list {
    position: absolute; left: 250px; top: 168px;
    list-style: none; color: var(--white); font-size: 11.5px; line-height: 20px;
  }
  .name-box {
    position: absolute; left: 0; top: 212px; width: 240px; height: 58px;
    background: var(--cyan); color: var(--white);
    padding: 9px 0 0 22px;
  }
  .name-box .name { font-weight: 700; font-size: 16px; line-height: 20px; }
  .name-box .role { font-size: 11.5px; line-height: 18px; }

  .back-circle {
    position: absolute; left: 215px; top: 30px; width: 260px; height: 260px;
    border-radius: 50%; background: var(--faint);
  }
  .card--back .wordmark { top: 118px; font-size: 62px; }
</style>
</head>
<body>
<div class="stage">

  <section class="card card--front" aria-label="Business card front">
    <div class="wordmark">BrivoTerna</div>
    <div class="contact-band"></div>
    <div class="icon-strip">
      <svg viewBox="0 0 12 12" aria-label="phone"><rect x="3" y="0.5" width="6" height="11" rx="1" fill="none" stroke="#fff" stroke-width="1.2"/><circle cx="6" cy="9.5" r="0.8" fill="#fff"/></svg>
      <svg viewBox="0 0 12 12" aria-label="email"><rect x="0.6" y="2.5" width="10.8" height="7" fill="none" stroke="#fff" stroke-width="1.2"/><path d="M0.6 2.5 L6 6.5 L11.4 2.5" fill="none" stroke="#fff" stroke-width="1.2"/></svg>
      <svg viewBox="0 0 12 12" aria-label="website"><circle cx="6" cy="6" r="5.2" fill="none" stroke="#fff" stroke-width="1.1"/><ellipse cx="6" cy="6" rx="2.3" ry="5.2" fill="none" stroke="#fff" stroke-width="1"/><path d="M0.8 6 H11.2" stroke="#fff" stroke-width="1"/></svg>
    </div>
    <ul class="contact-list">
      <li>+34 655.803.912</li>
      <li>teodoro.vinsquel@brivoterna-example.com</li>
      <li>www.brivoterna-example.com</li>
    </ul>
    <div class="name-box">
      <div class="name">Teodoro Vinsquel</div>
      <div class="role">CEO &amp; Founder</div>
    </div>
  </section>

  <section class="card card--back" aria-label="Business card back">
    <div class="back-circle"></div>
    <div class="wordmark">BrivoTerna</div>
  </section>

</div>
</body>
</html>
```